VELKO Website Redesign in Wix

Task:
Create a new design for all pages of the VELKO technology website in Wix. Specifications are:
Color palette preferences: black, white, gray, purple, blue. See VELKO Ref Doc provided.
Please refer to the VELKO_ref doc for a sample of the desired color palette
Typesetting must be in Montserrat
Brand will be that of a Marketing Technology company
Looking for vibrant, highly engaging images and organized, digestible flow. Open to suggestions
Required format is Wix.
VELKO logo does NOT need to be redesigned. Please use the files provided for the VELKO logo.
Look and feel
Each slider illustrates characteristics of the customer's brand and the style your logo design should communicate.

```html
<!DOCTYPE html>
<html lang="en">
<head>
<meta charset="utf-8">
<title>VELKO Tech</title>
<link href="https://fonts.googleapis.com/css2?family=Montserrat:wght@400;500;600;700;800&display=swap" rel="stylesheet">
<style>
:root{
  --blue:#3a32ee;
  --blue-deep:#2f28e6;
  --sky:#1eb4f6;
  --cyan:#22c4f8;
  --heading:#3a3ad6;
  --ink:#1b1b1b;
  --muted:#555;
  --white:#fff;
  --line:#cfd3e0;
}
*{margin:0;padding:0;box-sizing:border-box}
html,body{width:1200px;height:3992px;overflow:hidden}
body{position:relative;font-family:'Montserrat',sans-serif;background:var(--white);color:var(--ink)}
.abs{position:absolute}
.body-copy{font-family:Arial,Helvetica,sans-serif}

/* nav */
.nav{left:0;top:0;width:1200px;height:118px;background:var(--white)}
.brand{left:112px;top:32px;font-size:52px;font-weight:500;letter-spacing:12px;color:#111;line-height:1}
.nav-links{left:428px;top:54px;display:flex;gap:37px;font-size:14px;font-weight:500;color:#222}
.nav-links .active{color:var(--blue)}
.nav-cta{left:951px;top:37px;width:138px;height:52px;border-radius:26px;background:var(--sky);color:#fff;font-size:13px;font-weight:500;display:flex;align-items:center;justify-content:center}

/* hero */
.hero{left:0;top:118px;width:1200px;height:637px;background:linear-gradient(100deg,#22b8f6 0%,#2a8ff4 45%,#3a3cf0 100%)}
.hero-title{left:0;top:150px;width:1200px;text-align:center;font-size:72px;font-weight:800;color:#fff;line-height:1}
.hero-sub{left:0;top:244px;width:1200px;text-align:center;font-size:18px;color:#fff;line-height:29px}
.btn-outline{border:2px solid #fff;border-radius:30px;color:#fff;font-size:16px;font-weight:600;display:flex;align-items:center;justify-content:center}
.hero-btn{left:513px;top:320px;width:175px;height:52px}
.hero-frame{left:215px;top:398px;width:769px;height:539px;border:2px solid var(--cyan);border-radius:26px;background:#fff}
.hero-photo{left:245px;top:425px;width:710px;height:480px;border-radius:16px;background:linear-gradient(135deg,#c9dbe6 0%,#9fb2c2 45%,#5b6c7c 100%)}

/* strategy */
.section-title{font-weight:500;color:var(--heading)}
.rule{height:3px;background:var(--heading);width:52px}
.strat-title{left:112px;top:1058px;font-size:31px}
.strat-rule{left:112px;top:1104px}
.feature-icon{width:104px;height:104px;border-radius:50%;display:flex;align-items:center;justify-content:center}
.feature-icon.blue{background:var(--blue)}
.feature-icon.sky{background:var(--sky)}
.feature-name{font-size:22px;font-weight:500;color:#222}
.feature-text{font-size:13px;color:var(--muted);line-height:25px;width:428px;text-align:justify}
.phone{left:750px;top:1043px;width:296px;height:587px;border:2px solid var(--cyan);border-radius:22px;background:#fff}
.phone-screen{left:763px;top:1057px;width:271px;height:510px;border-radius:16px 16px 0 0;background:linear-gradient(160deg,#dfe4ea 0%,#b7c4cf 50%,#cfd8de 100%)}
.phone-logo{left:763px;top:1297px;width:271px;text-align:center;font-size:50px;font-weight:500;letter-spacing:8px;color:#111}
.phone-bar{left:763px;top:1567px;width:271px;height:50px;background:var(--blue-deep);border-radius:0 0 16px 16px;display:flex;justify-content:space-around;align-items:center}

/* platform */
.platform{left:0;top:1700px;width:1200px;height:537px;background:linear-gradient(180deg,#5a66f4 0%,#3a45f0 50%,#2a2ae8 100%)}
.platform-title{left:0;top:1788px;width:1200px;text-align:center;font-size:37px;font-weight:500;color:#fff}
.platform-rule{left:573px;top:1847px;width:54px;height:3px;background:#fff}
.platform-text{left:200px;top:1884px;width:800px;text-align:center;font-size:15px;color:#fff;line-height:31px}
.platform-btn{left:496px;top:2071px;width:207px;height:59px}

/* about */
.about-title{left:112px;top:2304px;font-size:41px}
.about-rule{left:112px;top:2362px}
.about-col{top:2398px;width:447px;font-size:13px;line-height:26.5px;color:#333;text-align:justify}

/* awards */
.awards{left:0;top:2662px;width:1200px;height:438px;background:linear-gradient(180deg,#22c6f8 0%,#1aa8f2 100%)}
.awards-word{left:140px;top:2705px;font-size:52px;font-weight:500;color:#fff}
.awards-divider{left:368px;top:2700px;width:2px;height:75px;background:#fff}
.badge{background:rgba(255,255,255,.85)}
.awards-rule{left:112px;top:2822px;width:977px;height:1px;background:rgba(255,255,255,.55)}
.testimonial-name{left:112px;top:2858px;font-size:17px;font-weight:600;color:#2a2fd8}
.testimonial-quote{left:143px;top:2906px;width:756px;font-size:16px;line-height:28.5px;color:#fff;text-align:justify}
.qmark{font-family:Georgia,serif;font-size:40px;font-weight:700;color:#fff;line-height:1}

/* demo */
.demo-title{left:110px;top:3170px;font-size:41px}
.demo-rule{left:110px;top:3232px}
.demo-sub{left:110px;top:3255px;font-size:19px;font-weight:500;color:#222}
.field{border:1px solid #b9bcc6;font-size:12px;font-weight:500;color:#222;padding:16px 15px}
.submit{left:112px;top:3567px;width:158px;height:53px;border-radius:27px;background:var(--blue);color:#fff;font-size:16px;font-weight:600;display:flex;align-items:center;justify-content:center}
.demo-art{left:660px;top:3185px;width:490px;height:445px;border-radius:48% 52% 40% 45%;background:radial-gradient(circle at 50% 50%,#dfe4fb 0%,#b9c3f4 60%,#eef0fc 100%)}

/* footer */
.footer{left:0;top:3670px;width:1200px;height:322px;background:var(--blue-deep)}
.footer-logo{left:136px;top:3774px;font-size:60px;font-weight:500;letter-spacing:11px;color:#fff;line-height:1}
.footer-divider{width:1px;background:rgba(255,255,255,.35)}
.footer-label{font-size:17px;font-weight:500;color:#fff}
.footer-text{font-size:14px;color:#fff;line-height:24px}
.social{width:42px;height:42px;border:2px solid #fff;border-radius:50%}
.copyright{left:0;top:3946px;width:1200px;text-align:center;font-size:13px;color:#fff}
</style>
</head>
<body>

<header class="abs nav"></header>
<div class="abs brand">VELKO</div>
<nav class="abs nav-links"><span class="active">HOME</span><span>HOW IT WORKS</span><span>VELKO APPLICATIONS</span><span>COMPANY</span></nav>
<div class="abs nav-cta">CONTACT US</div>

<section class="abs hero"></section>
<h1 class="abs hero-title">VELKO TECH</h1>
<p class="abs hero-sub">Increase and perfect your connection with consumers using VELKO™'s<br>patented self-service content delivery technology</p>
<div class="abs btn-outline hero-btn">LEARN MORE</div>
<div class="abs hero-frame"></div>
<div class="abs hero-photo" role="img" aria-label="Photo of hands holding a smartphone beside a laptop with floating shopping icons and a coffee cup"></div>

<h2 class="abs section-title strat-title">Strategy Towards Market Dominance</h2>
<div class="abs rule strat-rule"></div>

<div class="abs feature-icon blue" style="left:112px;top:1161px">
  <svg width="46" height="46" viewBox="0 0 46 46" fill="none" stroke="#fff" stroke-width="2.5"><rect x="3" y="3" width="40" height="40"/><path d="M12 34V24M20 34V18M28 34V12M36 34V20"/></svg>
</div>
<div class="abs feature-name" style="left:244px;top:1160px">Corporate Subscriptions</div>
<p class="abs feature-text body-copy" style="left:246px;top:1200px">Whether you're marketing software, selling a product, or looking to close a deal – find out your target market.</p>

<div class="abs feature-icon sky" style="left:112px;top:1325px">
  <svg width="56" height="50" viewBox="0 0 56 50" fill="none" stroke="#fff" stroke-width="2"><rect x="3" y="3" width="50" height="40" rx="3"/><path d="M3 12h50"/><circle cx="20" cy="28" r="9"/><path d="M11 28h18M20 19v18M32 22h14M32 28h14M32 34h10"/></svg>
</div>
<div class="abs feature-name" style="left:244px;top:1324px">Platform Integrations</div>
<p class="abs feature-text body-copy" style="left:246px;top:1364px">Our platform goes far beyond basic ad optimization to deliver content that immediately increases engagement</p>

<div class="abs feature-icon blue" style="left:112px;top:1488px">
  <svg width="58" height="46" viewBox="0 0 58 46" fill="none" stroke="#fff" stroke-width="2"><circle cx="6" cy="6" r="3"/><circle cx="6" cy="23" r="3"/><circle cx="6" cy="40" r="3"/><circle cx="18" cy="14" r="3"/><circle cx="18" cy="32" r="3"/><path d="M9 6h40M9 23h40M9 40h40M21 14h34M21 32h34"/></svg>
</div>
<div class="abs feature-name" style="left:244px;top:1487px">Technology Licensing</div>
<p class="abs feature-text body-copy" style="left:246px;top:1527px">Whether you're marketing software, selling a product, or looking to and quickly modify your campaigns to reach consumers</p>

<div class="abs phone"></div>
<div class="abs phone-screen" role="img" aria-label="Aerial view of a busy container port in pale grey-blue tones"></div>
<div class="abs phone-logo">VELKO</div>
<div class="abs phone-bar">
  <svg width="18" height="18" viewBox="0 0 18 18" fill="#fff"><path d="M9 2l7 7h-2v7h-4v-5H8v5H4V9H2z"/></svg>
  <svg width="18" height="14" viewBox="0 0 18 14" fill="none" stroke="#fff" stroke-width="1.5"><rect x="1" y="1" width="16" height="12"/><path d="M1 1l8 7 8-7"/></svg>
  <svg width="18" height="18" viewBox="0 0 18 18" fill="none" stroke="#fff" stroke-width="1.5"><path d="M3 2l3 1 1 4-2 1a9 9 0 005 5l1-2 4 1 1 3c-8 1-14-5-13-13z"/></svg>
  <svg width="16" height="18" viewBox="0 0 16 18" fill="none" stroke="#fff" stroke-width="1.5"><circle cx="8" cy="5" r="4"/><path d="M1 17c0-4 3-6 7-6s7 2 7 6z"/></svg>
  <svg width="20" height="16" viewBox="0 0 20 16" fill="none" stroke="#fff" stroke-width="1.5"><path d="M5 14H4a3 3 0 010-6 6 6 0 0112-1 3.5 3.5 0 010 7h-1M10 14V7M7 10l3-3 3 3"/></svg>
</div>

<section class="abs platform"></section>
<h2 class="abs platform-title">Our Revolutionary Platform</h2>
<div class="abs platform-rule"></div>
<div class="abs platform-text body-copy">
  <p>Whether you're marketing software, selling a product, or looking to close a deal – find out your target market and quickly modify your campaigns to reach consumers silently and securely.</p>
  <p style="margin-top:30px">Our platform goes far beyond basic ad optimization to deliver individualized content that immediately increases engagement over any communication medium with embedded tones.</p>
</div>
<div class="abs btn-outline platform-btn">GET STARTED</div>

<h2 class="abs section-title about-title">About us</h2>
<div class="abs rule about-rule"></div>
<p class="abs about-col body-copy" style="left:112px">VELKO™ Technology is a revolutionary platform that uses high frequency tones (known as VELKO packets) imperceptible to the human ear. VELKO's patented technology embeds information on an audio file for a more targeted, enhanced user experience via music, video, text, virtual reality, augmented reality, and other content. It is a modern-day solution to an age-old problem--establishing two-way communication with a consumer rather than listening to what they have to say.</p>
<p class="abs about-col body-copy" style="left:642px">VELKO™ Technology is a revolutionary platform that uses high frequency tones (known as VELKO packets) imperceptible to the human ear. VELKO's patented technology embeds information on an audio file for a more targeted, enhanced user experience via music, video, text, virtual reality, augmented reality, and other content. It is a modern-day solution to an age-old problem--establishing two-way communication with a consumer rather than listening to what they have to say.</p>

<section class="abs awards"></section>
<div class="abs awards-word">Awards</div>
<div class="abs awards-divider"></div>
<div class="abs badge" style="left:406px;top:2716px;width:196px;height:44px;border-radius:22px" role="img" aria-label="Partner award badge"></div>
<div class="abs badge" style="left:660px;top:2708px;width:150px;height:62px;border-radius:6px" role="img" aria-label="Partner award badge"></div>
<div class="abs badge" style="left:852px;top:2726px;width:237px;height:24px;border-radius:4px" role="img" aria-label="Partner award badge"></div>
<div class="abs awards-rule"></div>
<div class="abs testimonial-name">Marcus L. Fenwick &nbsp;&nbsp; | &nbsp;&nbsp; Founder,CEO</div>
<div class="abs qmark" style="left:111px;top:2908px">“</div>
<p class="abs testimonial-quote body-copy">Whether you're marketing software, selling a product, or looking to close a deal – find out your target market and quickly modify your campaigns to reach consumers silently and securely. Our platform goes far beyond basic ad optimization to deliver individualized content that immediately increases engagement over any communication medium with embedded tones. <span class="qmark" style="font-size:34px;vertical-align:-14px">”</span></p>

<h2 class="abs section-title demo-title">Request a Demo</h2>
<div class="abs rule demo-rule"></div>
<p class="abs demo-sub">Schedule a demo with one of our product consultants.</p>
<div class="abs field" style="left:112px;top:3315px;width:252px;height:47px">FIRST NAME</div>
<div class="abs field" style="left:380px;top:3315px;width:252px;height:47px">LAST NAME</div>
<div class="abs field" style="left:112px;top:3377px;width:252px;height:47px">EMAIL</div>
<div class="abs field" style="left:380px;top:3377px;width:252px;height:47px">PHONE</div>
<div class="abs field" style="left:112px;top:3437px;width:520px;height:108px">MESSAGE</div>
<div class="abs submit">SUBMIT</div>
<div class="abs demo-art" role="img" aria-label="Illustration of two people reviewing analytics charts on a large dashboard screen"></div>

<footer class="abs footer"></footer>
<div class="abs footer-logo">VELKO</div>
<div class="abs footer-divider" style="left:440px;top:3730px;height:120px"></div>
<div class="abs footer-divider" style="left:769px;top:3730px;height:120px"></div>
<svg class="abs" style="left:460px;top:3752px" width="18" height="24" viewBox="0 0 18 24" fill="none" stroke="#fff" stroke-width="1.5"><path d="M9 23S2 14 2 9a7 7 0 0114 0c0 5-7 14-7 14z"/><circle cx="9" cy="9" r="2.5"/></svg>
<div class="abs footer-label" style="left:500px;top:3748px">ADDRESS</div>
<p class="abs footer-text" style="left:500px;top:3772px">742 Maple Grove Avenue Suite<br>Brightwater 40219</p>
<div class="abs social" style="left:500px;top:3833px" role="img" aria-label="Professional network profile link"></div>
<div class="abs social" style="left:552px;top:3833px" role="img" aria-label="Social network page link"></div>
<svg class="abs" style="left:805px;top:3753px" width="20" height="20" viewBox="0 0 18 18" fill="none" stroke="#fff" stroke-width="1.3"><path d="M3 2l3 1 1 4-2 1a9 9 0 005 5l1-2 4 1 1 3c-8 1-14-5-13-13z"/></svg>
<div class="abs footer-label" style="left:845px;top:3748px">PHONE</div>
<p class="abs footer-text" style="left:845px;top:3772px">1-800-555-0147</p>
<svg class="abs" style="left:807px;top:3826px" width="20" height="15" viewBox="0 0 18 14" fill="none" stroke="#fff" stroke-width="1.3"><rect x="1" y="1" width="16" height="12"/><path d="M1 1l8 7 8-7"/></svg>
<div class="abs footer-label" style="left:847px;top:3818px">EMAIL</div>
<p class="abs footer-text" style="left:847px;top:3842px">info@velkotech.com</p>
<p class="abs copyright">© 2022 Velko.All rights reserved.</p>

</body>
</html>
```